BLPR Postcard Design: Mosquito Control, Lawn Maintenance and Pressure washing

I have a new company based in Atlanta,Georgia named Birchfield Lawn Pest Relief, LLC. We specializes in Mosquito Control. We also have additional services: Lawn maintenance, Pressure Washing and Gutter Cleaning. I would like to see designs with the colors Black, Red, Gray. We would like the customer to think of us when it comes to Enjoying a mosquito free yard and improving the look and feel of their home and lawn.

Industry/Entity Type

It Company

Requirements
Nice to have
• Treatment plans starting at $69/mt - front of card
• The additional services we offer - back of card.

```html
<!DOCTYPE html>
<html lang="en">
<head>
<meta charset="utf-8">
<title>BLPR Postcard</title>
<link rel="stylesheet" href="https://fonts.googleapis.com/css2?family=Lobster&family=Bebas+Neue&family=Baloo+2:wght@800&family=Archivo+Black&display=swap">
<style>
  :root {
    --red: #c4161c;
    --red-dark: #8e0f13;
    --charcoal: #2b2b2b;
    --black: #1c1c1c;
    --white: #ffffff;
    --rule: #d9d9d9;
    --stamp: #d4d4d4;
  }
  * { margin: 0; padding: 0; box-sizing: border-box; }
  html, body { width: 1200px; height: 930px; overflow: hidden; background: var(--white); }
  .canvas { position: relative; width: 1200px; height: 930px; background: var(--white); }

  .front { position: absolute; left: 0; top: 0; width: 580px; height: 766px; overflow: hidden; }

  .hero-photo {
    position: absolute; left: 0; top: 0; width: 580px; height: 355px;
    background: linear-gradient(100deg, #3f5a2c 0%, #6f8a4a 35%, #b9b3a8 60%, #d9d7d2 100%);
  }
  .headline { position: absolute; left: 58px; top: 40px; }
  .headline-script {
    font-family: "Lobster", cursive; font-size: 86px; line-height: 1;
    color: var(--red); text-shadow: 2px 3px 0 var(--white), 3px 5px 6px rgba(0,0,0,.35);
  }
  .headline-sub {
    font-family: "Baloo 2", sans-serif; font-weight: 800; font-size: 46px; line-height: 1;
    color: var(--red); margin-top: 2px;
    -webkit-text-stroke: 1px var(--white);
    text-shadow: 0 0 3px var(--white), 2px 2px 0 var(--white), -2px -2px 0 var(--white), 2px -2px 0 var(--white), -2px 2px 0 var(--white);
  }

  .services-band {
    position: absolute; left: 0; top: 355px; width: 580px; height: 43px;
    background: linear-gradient(var(--red), var(--red-dark));
    font-family: "Bebas Neue", sans-serif; font-size: 42px; line-height: 45px;
    color: var(--white); text-align: center; letter-spacing: .5px;
  }
  .services {
    position: absolute; left: 0; top: 398px; width: 580px; height: 160px;
    background: rgba(43,43,43,.95);
    display: flex; justify-content: space-between; padding: 14px 0 0;
  }
  .service { width: 193px; text-align: center; }
  .service-icon { width: 94px; height: 94px; display: block; margin: 0 auto; }
  .service-name {
    font-family: "Bebas Neue", sans-serif; font-size: 27px; color: var(--white);
    margin-top: 14px; letter-spacing: .3px;
  }

  .garden-photo {
    position: absolute; left: 0; top: 558px; width: 580px; height: 137px;
    background: linear-gradient(90deg, #4a3d33 0%, #6d5a49 25%, #6e9c3e 45%, #8dbb4d 75%, #a9a59a 100%);
  }
  .contact-bar {
    position: absolute; left: 0; top: 695px; width: 580px; height: 71px;
    background: var(--black);
    display: flex; align-items: center; justify-content: flex-end; padding-right: 28px; gap: 8px;
  }
  .phone-icon { width: 34px; height: 34px; }
  .phone-number { font-family: "Archivo Black", sans-serif; font-size: 42px; color: var(--white); letter-spacing: 1px; }

  .stamp-box { position: absolute; left: 908px; top: 30px; width: 265px; height: 265px; border: 2px solid var(--stamp); }
  .address-line { position: absolute; left: 645px; width: 497px; height: 2px; background: var(--rule); }
</style>
</head>
<body>
<div class="canvas">
  <section class="front">
    <div class="hero-photo" role="img" aria-label="Photo of a backyard with leafy trees beside a gray stucco house"></div>
    <div class="headline">
      <div class="headline-script">Enjoy a</div>
      <div class="headline-sub">mosquito free yard</div>
    </div>

    <div class="services-band">ADDITIONAL SERVICES</div>
    <div class="services">
      <div class="service">
        <svg class="service-icon" viewBox="0 0 94 94" aria-hidden="true">
          <defs><radialGradient id="disc" cx="40%" cy="35%" r="70%"><stop offset="0" stop-color="#e0262c"/><stop offset="1" stop-color="#8e0f13"/></radialGradient></defs>
          <circle cx="47" cy="47" r="45" fill="url(#disc)" stroke="#fff" stroke-opacity=".25" stroke-width="2"/>
          <path d="M24 32 L40 50" stroke="#fff" stroke-width="4" stroke-linecap="round"/>
          <path d="M34 50 H66 Q72 50 72 58 V62 H34 Z" fill="#fff"/>
          <circle cx="40" cy="66" r="6" fill="#fff" stroke="#b01419" stroke-width="2"/>
          <circle cx="66" cy="66" r="6" fill="#fff" stroke="#b01419" stroke-width="2"/>
        </svg>
        <div class="service-name">LAWN MAINTENANCE</div>
      </div>
      <div class="service">
        <svg class="service-icon" viewBox="0 0 94 94" aria-hidden="true">
          <circle cx="47" cy="47" r="45" fill="url(#disc)" stroke="#fff" stroke-opacity=".25" stroke-width="2"/>
          <path d="M70 22 L44 48" stroke="#fff" stroke-width="5" stroke-linecap="round"/>
          <path d="M40 44 L52 56 L44 64 L32 52 Z" fill="#fff"/>
          <path d="M36 58 L28 72 L34 74 L42 62 Z" fill="#fff"/>
        </svg>
        <div class="service-name">PRESSURE WASHING</div>
      </div>
      <div class="service">
        <svg class="service-icon" viewBox="0 0 94 94" aria-hidden="true">
          <circle cx="47" cy="47" r="45" fill="url(#disc)" stroke="#fff" stroke-opacity=".25" stroke-width="2"/>
          <path d="M47 20 Q42 28 42 31 A5 5 0 0 0 52 31 Q52 28 47 20 Z" fill="#fff"/>
          <rect x="28" y="40" width="38" height="8" fill="#fff"/>
          <path d="M42 48 V60 Q42 70 52 70 H62 V62 H54 Q52 62 52 60 V48 Z" fill="#fff"/>
        </svg>
        <div class="service-name">GUTTER CLEANING</div>
      </div>
    </div>

    <div class="garden-photo" role="img" aria-label="Photo of a garden patio with a chair, lawn and stepping stones"></div>
    <div class="contact-bar">
      <svg class="phone-icon" viewBox="0 0 34 34" aria-hidden="true">
        <circle cx="17" cy="17" r="16" fill="#c4161c"/>
        <path d="M12 9 L15 9 L16 14 L14 15.5 Q15.5 19 18.5 20 L20 18 L25 19 L25 22 Q25 25 22 25 Q10 24 9 12 Q9 9 12 9 Z" fill="#fff"/>
      </svg>
      <span class="phone-number">404-555-0186</span>
    </div>
  </section>

  <div class="stamp-box"></div>
  <div class="address-line" style="top:420px"></div>
  <div class="address-line" style="top:505px"></div>
  <div class="address-line" style="top:586px"></div>
  <div class="address-line" style="top:669px"></div>
</div>
</body>
</html>
```